Redesign business cards

We have a new logo and I am not that happy with the layout of our existing card and looking for a change. Font is a bit small and the green can be hard to read. Logo may need a tidy up as the copy I have is not that hi-res too so require you to produce a hi-res version of the logo for us too. There will be three individual business cards to produce with just the names and phone numbers being different. Address will change too, but use what you see on the card for now.

Industry/Entity Type

Business

Requirements
Nice to have
• You could consider a redesign to the new logo, just not too radical. We like the blue and green hexagons as we feel that they are representative of oil industry that we are in.

```html
<!DOCTYPE html>
<html lang="en">
<head>
<meta charset="utf-8">
<title>Norvale Oil Services – Business Cards</title>
<link href="https://fonts.googleapis.com/css2?family=Alegreya:wght@400;500&display=swap" rel="stylesheet">
<style>
  :root {
    --backdrop: #2a2a2a;
    --card: #ffffff;
    --ink: #5f5f5f;
    --ink-strong: #555555;
    --orange: #f7941d;
    --orange-soft: #f9c07a;
    --green-soft: #d3e8ac;
  }
  * { margin: 0; padding: 0; box-sizing: border-box; }
  html, body {
    width: 1200px;
    height: 1000px;
    overflow: hidden;
    background: var(--backdrop);
    font-family: "Alegreya", Georgia, serif;
  }
  .stage { position: relative; width: 1200px; height: 1000px; }
  .card {
    position: absolute;
    background: var(--card);
    box-shadow: 0 10px 30px rgba(0,0,0,.45);
    overflow: hidden;
  }

  /* Portrait front card */
  .card--front { left: 70px; top: 170px; width: 420px; height: 670px; }
  .card--front .brand { position: absolute; left: 40px; top: 92px; display: flex; align-items: center; gap: 14px; }
  .brand-dot { width: 40px; height: 40px; border-radius: 50%; background: var(--orange); flex: none; }
  .brand-name { color: var(--ink); font-weight: 500; line-height: 1; }
  .card--front .brand-name { font-size: 38px; }
  .holder { position: absolute; left: 0; right: 0; top: 330px; text-align: center; color: var(--ink); }
  .holder-name { font-size: 21px; }
  .holder-role { font-size: 17px; margin-top: 2px; }
  .contact-list { position: absolute; left: 62px; top: 560px; list-style: none; color: var(--ink); font-size: 17px; }
  .contact-list li { display: flex; align-items: center; gap: 12px; height: 25px; }
  .contact-list li::before { content: ""; width: 16px; height: 16px; border-radius: 50%; background: var(--orange); flex: none; }
  .corner-accent { position: absolute; right: -70px; bottom: -80px; width: 260px; height: 260px; border-radius: 50%; background: var(--orange-soft); opacity: .8; }

  /* Landscape back card */
  .card--back { left: 520px; top: 300px; width: 640px; height: 380px; }
  .card--back .brand { position: absolute; left: 60px; top: 110px; display: flex; align-items: center; gap: 24px; }
  .card--back .brand-dot { width: 80px; height: 80px; }
  .card--back .brand-name { font-size: 60px; }
  .address { position: absolute; left: 0; right: 0; bottom: 48px; text-align: center; color: var(--orange); font-size: 16px; }
</style>
</head>
<body>
<main class="stage">
  <section class="card card--front" aria-label="Business card front">
    <div class="brand">
      <span class="brand-dot"></span>
      <span class="brand-name">Norvale Oil Services</span>
    </div>
    <div class="holder">
      <p class="holder-name">Daniel Whitcombe NZCE (Mech) P&amp;P</p>
      <p class="holder-role">Director</p>
    </div>
    <ul class="contact-list">
      <li>+614 555 0142</li>
      <li>daniel@norvale.co.nz</li>
      <li>www.norvale.com.au</li>
    </ul>
    <span class="corner-accent"></span>
  </section>

  <section class="card card--back" aria-label="Business card back">
    <div class="brand">
      <span class="brand-dot"></span>
      <span class="brand-name">Norvale Oil Services</span>
    </div>
    <p class="address">Norvale Oil Services 412 Harbour Road | PO Box 5170 | Kangaroo Point Queensland 4169</p>
  </section>
</main>
</body>
</html>
```